Stationery Design Project for Nimbora, Chicago

Nimbora, a street parking application which helps car drivers find a street parking spot by offering an ideal path along which to look for parking. This path is calculated by our algorithm based on data (e.g. historical data, baseball games schedule, etc.). Along this path the driver will find a spot and will also save 70% of the search time. Customer we target is reg. between 21 and 45 yo.

We envision something young, fresh, bright and original. Slightly abstract maybe. It should represent the idea and elements of finding street parking in the city, e.g. car(s), parking spot, people, city, etc. (just ideas!).

Logo is attached.

Requirement:
- Business Cards (2 Sided Full Color CMYK)
- Letterhead (1 Sided Full Color CMYK)
- Envelope (1 Sided Full Color CMYK)
- Sticker (1 Sided Full Color CMYK), round with a 2inch diameter.

Reason: We're starting to get more and more designs and need more time to look into all of them. Very exciting!! Thanks to everybody!

Hi all, we're in the process of selecting our favs. Though choices!!! Really good submissions. Will keep you posted and sorry for the delay.

Target Market(s)

Car drivers and owners between 21 and 45

Industry/Entity Type

Parking

Requirements
Must have
• Sticker should be round and include company URL nimbora.com and the new logo which we will attach soon.
Should not have
• Should not be too serious or boring.

```html
<!DOCTYPE html>
<html lang="en">
<head>
<meta charset="utf-8">
<title>Nimbora Business Card</title>
<link rel="stylesheet" href="https://fonts.googleapis.com/css2?family=Open+Sans:wght@400;600;700&display=swap">
<style>
  :root {
    --backdrop: #d8d2c8;
    --card: #ffffff;
    --card-edge: #b9b2a8;
    --name-ink: #5b5aa3;
    --title-ink: #6b6aa8;
    --brand-ink: #2b2b2e;
    --body-ink: #3a3a3a;
    --rule: #9a9a9a;
    --mark-blue: #1f62c9;
    --band-blue-a: #2a3f8f;
    --band-blue-b: #2fa6e6;
    --band-dark-a: #6f6f73;
    --band-dark-b: #1d1d20;
  }
  * { box-sizing: border-box; margin: 0; padding: 0; }
  html, body {
    width: 1200px; height: 396px; overflow: hidden;
    background: var(--backdrop);
    font-family: "Open Sans", Arial, sans-serif;
  }
  .canvas { position: relative; width: 1200px; height: 396px; }
  .card {
    position: absolute; top: 47px;
    width: 516px; height: 297px;
    background: var(--card);
    border: 1px solid var(--card-edge);
    overflow: hidden;
  }
  .card--front { left: 59px; }
  .card--back { left: 622px; }

  .holder {
    position: absolute; top: 12px; left: 0; width: 100%;
    text-align: center; color: var(--name-ink);
    font-size: 21px; font-weight: 700;
  }
  .holder .holder-title { font-size: 16px; font-weight: 400; color: var(--title-ink); }

  .brand { position: absolute; display: flex; align-items: center; }
  .brand-dot {
    width: 90px; height: 90px; border-radius: 50%;
    background: var(--mark-blue);
    flex: none;
  }
  .brand-name {
    margin-left: 18px;
    font-size: 58px; font-weight: 600; letter-spacing: 0.5px;
    color: var(--brand-ink); line-height: 1;
  }
  .card--front .brand { left: 98px; top: 67px; }
  .card--back .brand { left: 110px; top: 95px; }

  .address {
    position: absolute; right: 248px; top: 205px;
    text-align: right; font-size: 13px; line-height: 18px; color: var(--body-ink);
  }
  .divider {
    position: absolute; left: 283px; top: 183px;
    width: 1px; height: 80px; background: var(--rule);
  }
  .contacts {
    position: absolute; left: 296px; top: 186px;
    list-style: none; font-size: 13px; color: var(--body-ink);
  }
  .contacts li { display: flex; align-items: center; height: 19px; }
  .contacts svg { width: 10px; height: 10px; margin-right: 8px; fill: var(--body-ink); }

  .band {
    position: absolute; left: 0; bottom: 0; width: 100%; height: 11px;
  }

  .site {
    position: absolute; left: 0; top: 226px; width: 100%;
    text-align: center; font-size: 16px; letter-spacing: 1.5px; color: var(--body-ink);
  }
</style>
</head>
<body>
<main class="canvas">

  <section class="card card--front" aria-label="Business card front">
    <p class="holder">Your Name , <span class="holder-title">Title</span></p>

    <div class="brand">
      <span class="brand-dot"></span>
      <span class="brand-name">Nimbora</span>
    </div>

    <address class="address" style="font-style:normal">
      Complex Name, Street Name<br>
      Area, City Name,000 000
    </address>

    <span class="divider"></span>

    <ul class="contacts">
      <li>
        <svg viewBox="0 0 10 10"><path d="M2 0.5 L4 2.5 L3 3.8 Q4.2 5.8 6.2 7 L7.5 6 L9.5 8 L8 9.5 Q3.5 9 0.5 2 Z"/></svg>
        +1 312 555 0147
      </li>
      <li>
        <svg viewBox="0 0 10 10"><path d="M2.5 0 H7.5 V10 H2.5 Z M3.3 1 V7.5 H6.7 V1 Z M4.5 8.2 H5.5 V9.2 H4.5 Z"/></svg>
        +1 312 555 0147
      </li>
      <li>
        <svg viewBox="0 0 10 10"><path d="M0 2 H10 V8.5 H0 Z M0.8 2.6 L5 5.6 L9.2 2.6 Z"/></svg>
        info@nimbora.com
      </li>
      <li>
        <svg viewBox="0 0 10 10"><circle cx="5" cy="5" r="4.5"/></svg>
        www.nimbora.com
      </li>
    </ul>

    <svg class="band" viewBox="0 0 516 11" preserveAspectRatio="none" aria-hidden="true">
      <defs>
        <linearGradient id="bandBlue" x1="0" x2="1" y1="0" y2="0">
          <stop offset="0" stop-color="var(--band-blue-a)"/>
          <stop offset="1" stop-color="var(--band-blue-b)"/>
        </linearGradient>
        <linearGradient id="bandDark" x1="0" x2="1" y1="0" y2="0">
          <stop offset="0" stop-color="var(--band-dark-a)"/>
          <stop offset="1" stop-color="var(--band-dark-b)"/>
        </linearGradient>
      </defs>
      <polygon points="0,0 268,0 258,11 0,11" fill="url(#bandBlue)"/>
      <polygon points="280,0 516,0 516,11 270,11" fill="url(#bandDark)"/>
    </svg>
  </section>

  <section class="card card--back" aria-label="Business card back">
    <div class="brand">
      <span class="brand-dot"></span>
      <span class="brand-name">Nimbora</span>
    </div>
    <p class="site">www.nimbora.com</p>
  </section>

</main>
</body>
</html>
```